Business Card Design

We are a commercial real estate brokerage in San Francisco, leasing office buildings downtown.
I would like a clean, elegant look. Simple but powerful .

Industry/Entity Type

Business

Contact Information for Business Card

Derek Holloway
lic# 07258143
415.555.0172
derek@velt-commercial.example
velt-commercial.example

```html
<!DOCTYPE html>
<html lang="en">
<head>
<meta charset="UTF-8">
<title>Velt Commercial — Business Card</title>
<link href="https://fonts.googleapis.com/css2?family=Arimo:wght@400;700&display=swap" rel="stylesheet">
<style>
  :root {
    --page-bg: #e9eaed;
    --brand-blue: #7687a9;
    --name-blue: #7b8db1;
    --card-white: #ffffff;
    --text-grey: #5a5d63;
    --skyline-light: #eef0f3;
    --skyline-mid: #dfe2e7;
    --on-blue: #ffffff;
  }
  * { margin: 0; padding: 0; box-sizing: border-box; }
  html, body {
    width: 1200px;
    height: 950px;
    overflow: hidden;
    background: var(--page-bg);
    font-family: "Arimo", Arial, sans-serif;
  }
  .canvas {
    position: relative;
    width: 1200px;
    height: 950px;
  }
  .card {
    position: absolute;
    width: 700px;
    height: 400px;
    box-shadow: 0 6px 24px rgba(0,0,0,0.18);
    overflow: hidden;
  }

  /* Back of card */
  .card-back {
    left: 150px;
    top: 50px;
    background: var(--brand-blue);
    color: var(--on-blue);
  }
  .card-back .wordmark {
    position: absolute;
    left: 0;
    right: 0;
    top: 135px;
    display: flex;
    justify-content: center;
    align-items: center;
    gap: 16px;
  }
  .card-back .tagline {
    position: absolute;
    left: 0;
    right: 0;
    top: 250px;
    text-align: center;
    font-size: 17px;
    line-height: 1.45;
  }

  /* Wordmark shared */
  .wordmark-square {
    width: 34px;
    height: 34px;
    background: currentColor;
  }
  .wordmark-name {
    font-weight: 700;
    font-size: 36px;
    letter-spacing: 2px;
    line-height: 1;
  }

  /* Front of card */
  .card-front {
    left: 350px;
    top: 500px;
    background: var(--card-white);
    color: var(--text-grey);
  }
  .card-front .skyline {
    position: absolute;
    left: 0;
    top: 0;
    width: 100%;
    height: 100%;
  }
  .card-front .accent-bar {
    position: absolute;
    left: 0;
    top: 118px;
    width: 14px;
    height: 48px;
    background: var(--brand-blue);
  }
  .agent {
    position: absolute;
    left: 48px;
    top: 116px;
  }
  .agent-name {
    font-weight: 700;
    font-size: 27px;
    color: var(--name-blue);
  }
  .agent-license {
    margin-top: 6px;
    font-size: 19px;
  }
  .contact {
    position: absolute;
    left: 48px;
    bottom: 42px;
    list-style: none;
    font-size: 18px;
    line-height: 1.5;
  }
  .card-front .wordmark {
    position: absolute;
    right: 44px;
    top: 150px;
    display: flex;
    align-items: center;
    gap: 14px;
    color: var(--name-blue);
  }
  .card-front .wordmark-name { font-size: 32px; }
  .card-front .wordmark-square { width: 30px; height: 30px; }
</style>
</head>
<body>
<main class="canvas">

  <section class="card card-back" aria-label="Business card back">
    <div class="wordmark">
      <span class="wordmark-square"></span>
      <span class="wordmark-name">VELT COMMERCIAL</span>
    </div>
    <p class="tagline">commercial real estate brokerage in San Francisco<br>leasing office buildings downtown.</p>
  </section>

  <section class="card card-front" aria-label="Business card front">
    <svg class="skyline" viewBox="0 0 700 400" role="img" aria-label="Faint downtown office tower skyline illustration">
      <defs>
        <linearGradient id="skyline-fade" x1="0" y1="0" x2="1" y2="1">
          <stop offset="0" stop-color="var(--card-white)"/>
          <stop offset="0.45" stop-color="var(--skyline-light)"/>
          <stop offset="1" stop-color="var(--skyline-mid)"/>
        </linearGradient>
      </defs>
      <rect width="700" height="400" fill="url(#skyline-fade)"/>
    </svg>
    <span class="accent-bar"></span>
    <div class="agent">
      <h1 class="agent-name">Derek Holloway</h1>
      <p class="agent-license">lic# 07258143</p>
    </div>
    <ul class="contact">
      <li>415.555.0172</li>
      <li>derek@velt-commercial.example</li>
      <li>velt-commercial.example</li>
    </ul>
    <div class="wordmark">
      <span class="wordmark-square"></span>
      <span class="wordmark-name">VELT COMMERCIAL</span>
    </div>
  </section>

</main>
</body>
</html>
```